Medical Billing Company Needs a Business Card Design

We need a business card design for a Florida based medical billing company called 'Clinicians Keystone Solutions'. We specialize in providing revenue cycle management services to physician and therapist offices (we're basically their back-office processing partner for providing billing software, claims submissions, A/R follow-up and patient statements & collections. Our logo is red and blue-ish, so make sure that whatever other elements are used will match appropriately. Our current business card design has a too small font size. I'd like to project an image that shows we are modern & reliable. On a side note, I'm planning on using ZUB for printing these cards.

Target Market(s)

Office managers, physicians, therapists

Industry/Entity Type

Printing

Requirements
Must have
• Logo
Name of Employee
Phone
Fax
E-mail
Website

```html
<!DOCTYPE html>
<html lang="en">
<head>
<meta charset="utf-8">
<title>Clinicians Keystone – Business Card</title>
<link href="https://fonts.googleapis.com/css2?family=Open+Sans:wght@400;600;700&display=swap" rel="stylesheet">
<style>
  :root {
    --navy: #2b2a82;
    --violet: #4b3f9c;
    --crimson: #b0202a;
    --ink: #3a3a3a;
    --paper: #ffffff;
    --backdrop: #ecebe8;
    --edge: #d9d9d9;
  }
  * { box-sizing: border-box; margin: 0; padding: 0; }
  html, body {
    width: 1200px; height: 720px; overflow: hidden;
    background: var(--backdrop);
    font-family: "Open Sans", Arial, sans-serif;
  }
  .canvas {
    width: 1200px; height: 720px;
    display: flex; align-items: center; justify-content: center; gap: 40px;
  }
  .card {
    position: relative;
    width: 540px; height: 309px;
    background: var(--paper);
    border: 1px solid var(--edge);
    box-shadow: 0 6px 18px rgba(0,0,0,.12);
  }
  /* Front */
  .card__band {
    position: absolute; left: 0; top: 0;
    width: 14px; height: 100%;
  }
  .brand-name {
    font-weight: 600;
    letter-spacing: 2px;
    color: var(--navy);
    text-transform: uppercase;
    white-space: nowrap;
  }
  .front .brand-name {
    position: absolute; left: 40px; top: 66px;
    font-size: 25px;
  }
  .employee {
    position: absolute; right: 36px; top: 64px;
    text-align: right;
  }
  .employee__name { color: var(--violet); font-weight: 700; font-size: 17px; line-height: 1.1; }
  .employee__title { color: var(--crimson); font-size: 12px; }
  .contact {
    position: absolute; left: 40px; top: 150px;
    list-style: none;
    color: var(--ink); font-size: 13.5px; line-height: 21px;
  }
  .contact li { display: flex; align-items: center; gap: 7px; }
  .contact svg { width: 13px; height: 13px; flex: none; }
  .address {
    position: absolute; left: 40px; top: 245px;
    color: var(--ink); font-size: 13.5px; line-height: 19px;
    font-style: normal;
  }
  /* Back */
  .back { display: flex; flex-direction: column; align-items: center; justify-content: center; }
  .back .brand-name { font-size: 30px; margin-bottom: 40px; }
  .back__site {
    font-size: 15px; letter-spacing: 4px; color: var(--ink);
  }
</style>
</head>
<body>
<main class="canvas">
  <section class="card front" aria-label="Card front">
    <svg class="card__band" viewBox="0 0 14 309" preserveAspectRatio="none" aria-hidden="true">
      <polygon points="0,0 14,0 14,110 0,126" fill="#b0202a"/>
      <polygon points="0,132 14,116 14,309 0,309" fill="#2b2a82"/>
    </svg>
    <div class="brand-name">Clinicians Keystone</div>
    <div class="employee">
      <div class="employee__name">Your Name</div>
      <div class="employee__title">Title</div>
    </div>
    <ul class="contact">
      <li><svg viewBox="0 0 16 16" aria-hidden="true"><circle cx="8" cy="8" r="7" fill="none" stroke="#2b2a82" stroke-width="1.6"/><path d="M5 4.5l2 2-1 1.2c.7 1.3 1.5 2.1 2.8 2.8l1.2-1 2 2-1.3 1.3C7.5 12.5 3.5 8.5 3.7 5.8z" fill="#2b2a82"/></svg>123-456-0789</li>
      <li><svg viewBox="0 0 16 16" aria-hidden="true"><rect x="4.5" y="1" width="7" height="14" rx="1.5" fill="#2b2a82"/><rect x="6" y="3" width="4" height="7" fill="#fff"/></svg>123-456-0789</li>
      <li><svg viewBox="0 0 16 16" aria-hidden="true"><rect x="1" y="3" width="14" height="10" rx="1.5" fill="#2b2a82"/><path d="M1.5 4l6.5 5 6.5-5" fill="none" stroke="#fff" stroke-width="1.3"/></svg>info@cliniciankeystone.com</li>
      <li><svg viewBox="0 0 16 16" aria-hidden="true"><circle cx="8" cy="8" r="7" fill="#2b2a82"/><path d="M1 8h14M8 1c-3 3.5-3 10.5 0 14M8 1c3 3.5 3 10.5 0 14" fill="none" stroke="#fff" stroke-width="1"/></svg>www.cliniciankeystone.com</li>
    </ul>
    <address class="address">Street Name, City Name<br>State Zip Code</address>
  </section>

  <section class="card back" aria-label="Card back">
    <div class="brand-name">Clinicians Keystone</div>
    <div class="back__site">www.cliniciankeystone.com</div>
  </section>
</main>
</body>
</html>
```